Brightmill Data Works

Our company is about IT hardwares and IT solutions. IT hardware such as PC, RAMS, storage and servers. IT solutions such as project management, BA. We are also selling new technology too.

Target Market(s)

Consumer, Small to Medium Business, Corporate

Requirements
Must have
• The business card must have the following:
• Name:
• Title:
• Contact Number:
• Email address:
• Website:
• Color: Must match the logo color upgrade

```html
<!DOCTYPE html>
<html lang="en">
<head>
<meta charset="utf-8">
<title>Brightmill Data Works – Business Card</title>
<link href="https://fonts.googleapis.com/css2?family=Saira+Semi+Condensed:wght@700&family=Open+Sans:wght@400;600&display=swap" rel="stylesheet">
<style>
  :root {
    --stage: #2b2b2b;
    --card-white: #f7f7f7;
    --card-shade: #e6e6e6;
    --band: #3d3d3f;
    --ink: #3a3a3c;
    --gold: #c98c3a;
    --light: #e9e9e9;
  }
  html, body {
    margin: 0;
    width: 1200px;
    height: 997px;
    overflow: hidden;
    background: var(--stage);
  }
  .canvas {
    position: relative;
    width: 1200px;
    height: 997px;
  }
  .card {
    position: absolute;
    left: 330px;
    width: 540px;
    height: 309px;
    border-radius: 22px;
    overflow: hidden;
    background: linear-gradient(160deg, var(--card-white) 40%, var(--card-shade));
    box-shadow: 0 10px 30px rgba(0,0,0,0.45);
  }
  .card--front { top: 150px; }
  .card--back { top: 530px; }
  .card__art {
    position: absolute;
    inset: 0;
    width: 540px;
    height: 309px;
  }
  .brand {
    position: absolute;
    display: flex;
    align-items: center;
    gap: 14px;
    font-family: "Saira Semi Condensed", sans-serif;
    font-weight: 700;
    color: var(--ink);
    letter-spacing: 1px;
    line-height: 1.05;
  }
  .brand__name span { display: block; }
  .brand__dot {
    flex: none;
    width: 22px;
    height: 22px;
    border-radius: 50%;
    background: var(--gold);
  }
  .card--front .brand { left: 60px; top: 48px; font-size: 32px; }
  .card--back .brand { left: 0; right: 0; top: 40px; justify-content: center; text-align: center; font-size: 38px; }
  .website {
    position: absolute;
    right: 40px;
    bottom: 30px;
    font-family: "Open Sans", sans-serif;
    font-weight: 600;
    font-size: 14px;
    letter-spacing: 1px;
    color: var(--light);
  }
  .person {
    position: absolute;
    left: 120px;
    top: 238px;
    font-family: "Open Sans", sans-serif;
    text-align: right;
    width: 150px;
  }
  .person__name {
    color: var(--gold);
    font-size: 15px;
    letter-spacing: 0.5px;
  }
  .person__title {
    color: var(--light);
    font-size: 12px;
  }
  .divider {
    position: absolute;
    left: 285px;
    top: 228px;
    width: 1.5px;
    height: 52px;
    background: var(--gold);
  }
  .contacts {
    position: absolute;
    left: 302px;
    top: 222px;
    margin: 0;
    padding: 0;
    list-style: none;
    font-family: "Open Sans", sans-serif;
    font-size: 13px;
    color: var(--light);
  }
  .contacts li {
    display: flex;
    align-items: center;
    gap: 10px;
    height: 26px;
  }
  .contacts svg { width: 17px; height: 17px; }
</style>
</head>
<body>
<main class="canvas">

  <section class="card card--front" aria-label="Business card front">
    <svg class="card__art" viewBox="0 0 540 309" aria-hidden="true">
      <path d="M0,309 L0,292 Q210,160 540,128 L540,309 Z" fill="var(--band)"/>
      <path d="M22,272 Q230,150 505,118" fill="none" stroke="var(--gold)" stroke-width="4" stroke-linecap="round"/>
    </svg>
    <div class="brand"><span class="brand__dot"></span><div class="brand__name"><span>BRIGHTMILL</span><span>DATA WORKS</span></div></div>
    <div class="website">www.brightmilldataworks.com</div>
  </section>

  <section class="card card--back" aria-label="Business card back">
    <svg class="card__art" viewBox="0 0 540 309" aria-hidden="true">
      <path d="M0,309 L0,292 Q210,160 540,128 L540,309 Z" fill="var(--band)"/>
      <path d="M22,272 Q230,150 505,118" fill="none" stroke="var(--gold)" stroke-width="4" stroke-linecap="round"/>
    </svg>
    <div class="brand"><div class="brand__name"><span>BRIGHTMILL</span><span>DATA WORKS</span></div></div>
    <div class="person">
      <div class="person__name">MARCUS LIN</div>
      <div class="person__title">Managing Director</div>
    </div>
    <div class="divider"></div>
    <ul class="contacts">
      <li>
        <svg viewBox="0 0 20 20" aria-hidden="true"><circle cx="10" cy="10" r="9" fill="none" stroke="var(--gold)" stroke-width="1.5"/><path d="M6 8 Q10 5 14 8 L13 10 L11 9 L9 9 L7 10 Z M7 11 H13 V14 H7 Z" fill="var(--gold)"/></svg>
        <span>9412 3085</span>
      </li>
      <li>
        <svg viewBox="0 0 20 20" aria-hidden="true"><circle cx="10" cy="10" r="9" fill="none" stroke="var(--gold)" stroke-width="1.5"/><rect x="5.5" y="6.5" width="9" height="7" fill="none" stroke="var(--gold)" stroke-width="1.3"/><path d="M5.5 6.5 L10 10.5 L14.5 6.5" fill="none" stroke="var(--gold)" stroke-width="1.3"/></svg>
        <span>mlin@brightmilldata.com</span>
      </li>
    </ul>
  </section>

</main>
</body>
</html>
```